Construction company that specializes in roofing and siding

https://maplecrestbuild.example/featured-projects/

https://www.bramwickhomesllc.example/#

https://www.tallgrovecontractors.example/residential-siding-services/

Please model a website after these examples
I posted a doc that has some content to get you started. I will upload more content and photos as the site progresses.

Coded - Design and coding required

5+ page

```html
<!DOCTYPE html>
<html lang="en">
<head>
<meta charset="utf-8">
<title>Stoneguard Construction</title>
<link href="https://fonts.googleapis.com/css2?family=Syncopate:wght@700&family=Poppins:wght@400;500;600;700&family=Open+Sans:wght@400&display=swap" rel="stylesheet">
<style>
:root{
  --ink:#1d1d1f;
  --dark:#2b2b2d;
  --panel:#4b4e55;
  --teal:#0f6e63;
  --gray-btn:#8b8b8d;
  --section:#eef0f3;
  --star:#e0a21a;
  --muted:#444;
  --white:#fff;
}
*{box-sizing:border-box;margin:0;padding:0}
html,body{width:1200px;height:3681px;overflow:hidden}
body{position:relative;font-family:"Poppins",sans-serif;color:var(--ink);background:var(--white)}
.abs{position:absolute}
.display{font-family:"Syncopate",sans-serif;font-weight:700;letter-spacing:1px}

/* header */
.site-header{left:0;top:0;width:1200px;height:86px;background:var(--dark)}
.brand{display:flex;align-items:center;gap:12px;color:var(--white);font-weight:600}
.brand-dot{width:46px;height:46px;border-radius:50%;background:#6b6d72}
.brand-name{font-size:16px;line-height:1.15;letter-spacing:2px}
.nav{top:29px;display:flex;gap:0;color:var(--white);font-size:16px}
.nav a{position:absolute;white-space:nowrap;color:var(--white);text-decoration:none}
.btn-outline-light{left:923px;top:20px;width:166px;height:44px;border:2px solid var(--white);border-radius:22px;color:var(--white);font-size:15px;font-weight:600;display:flex;align-items:center;justify-content:center}

/* hero */
.hero-photo{left:0;top:86px;width:1200px;height:600px;background:linear-gradient(180deg,#8fa0a8 0%,#6d7a73 35%,#4d5a45 60%,#5f8a3a 85%,#6f9a45 100%)}
.hero-tag{left:80px;top:274px;width:430px;height:50px;background:var(--teal);color:var(--white);font-weight:700;font-size:19px;display:flex;align-items:center;justify-content:center}
.hero-title{left:80px;top:348px;color:var(--white);font-size:38px;line-height:60px}
.quote-panel{left:556px;top:214px;width:578px;height:326px;background:var(--panel);border-radius:12px}
.quote-panel h2{position:absolute;left:30px;top:24px;color:var(--white);font-size:28px;font-weight:700}
.field{position:absolute;background:var(--white);border-radius:3px;font-size:10px;color:#777;padding:10px 8px}
.field.select::after{content:"⌄";position:absolute;right:12px;top:6px;font-size:12px}
.btn-quote{position:absolute;left:30px;top:262px;width:145px;height:37px;border:2px solid var(--white);border-radius:19px;color:var(--white);font-size:12px;font-weight:600;display:flex;align-items:center;justify-content:center}

/* about */
.about-title{left:113px;top:778px;font-size:30px}
.about-sub{left:113px;top:832px;font-size:21px}
.about-copy{left:113px;top:874px;width:455px;font-family:"Open Sans",sans-serif;font-size:15.5px;line-height:26.5px;color:var(--muted)}
.about-copy p+p{margin-top:26px}
.btn-gray{height:43px;border-radius:22px;background:var(--gray-btn);color:var(--white);font-weight:500;font-size:15px;display:flex;align-items:center;justify-content:center}
.about-photo{left:630px;top:771px;width:459px;height:433px;background:linear-gradient(135deg,#cf7a52 0%,#b9552f 45%,#2f6e4c 70%,#3a3a3a 100%)}

/* services */
.services{left:0;top:1290px;width:1200px;height:1431px;background:var(--section)}
.section-title{width:1200px;left:0;text-align:center;font-size:30px}
.service-photo{width:468px;height:309px}
.service-name{font-size:24px;font-weight:500}
.service-copy{width:470px;font-size:13.5px;line-height:25px;color:#333}
.btn-outline{width:128px;height:43px;border:2px solid #333;border-radius:22px;font-size:14px;font-weight:500;display:flex;align-items:center;justify-content:center}

/* reviews */
.review-card{width:309px;height:343px;background:var(--white);box-shadow:0 4px 18px rgba(0,0,0,.08)}
.review-card .mark{position:absolute;left:34px;top:20px;font-size:90px;line-height:1;color:#e6e6e6;font-family:Georgia,serif}
.review-card .text{position:absolute;left:36px;top:66px;width:247px;font-size:15px;line-height:26px;color:#555;text-align:justify}
.review-card .name{position:absolute;left:0;width:309px;top:250px;text-align:center;font-size:17px;font-weight:500}
.review-card .stars{position:absolute;left:0;width:309px;top:277px;text-align:center;color:var(--star);font-size:17px;letter-spacing:1px}
.arrow{width:40px;height:77px;display:flex;align-items:center;justify-content:center}

/* footer */
.site-footer{left:0;top:3307px;width:1200px;height:374px;background:var(--dark);color:var(--white)}
.footer-links{left:0;top:3478px;width:1200px;text-align:center;font-size:17px}
.social{top:3529px;display:flex;gap:6px;left:496px}
.social span{width:37px;height:37px;border:1.5px solid var(--white);border-radius:50%}
.footer-rule{left:111px;top:3597px;width:978px;height:1px;background:#4a4a4c}
.copyright{left:0;top:3620px;width:1200px;text-align:center;font-size:13px}
</style>
</head>
<body>

<header class="abs site-header">
  <div class="abs brand" style="left:111px;top:20px">
    <span class="brand-dot"></span>
    <span class="brand-name">STONEGUARD<br>CONSTRUCTION</span>
  </div>
  <nav class="abs nav" style="left:0;width:900px">
    <a style="left:500px">Home</a>
    <a style="left:574px">What we do ▾</a>
    <a style="left:707px">About us</a>
    <a style="left:804px">Contact Us</a>
  </nav>
  <div class="abs btn-outline-light">START FREE QUOTE</div>
</header>

<section>
  <div class="abs hero-photo" role="img" aria-label="Two-storey suburban house with grey shingle roof, green lawn and shrubs"></div>
  <div class="abs hero-tag">ROOFING | SIDING | WINDOWS | GUTTERS</div>
  <h1 class="abs display hero-title">STONEGUARD<br>CONSTRUCTION</h1>
  <form class="abs quote-panel">
    <h2>GET IN TOUCH</h2>
    <div class="field" style="left:30px;top:76px;width:162px;height:34px">First Name</div>
    <div class="field" style="left:205px;top:76px;width:162px;height:34px">Last Name</div>
    <div class="field select" style="left:380px;top:76px;width:163px;height:34px">Choose Services</div>
    <div class="field" style="left:30px;top:125px;width:162px;height:34px">Phone</div>
    <div class="field" style="left:205px;top:125px;width:162px;height:34px">Email</div>
    <div class="field" style="left:380px;top:125px;width:163px;height:34px">Zip</div>
    <div class="field" style="left:30px;top:177px;width:513px;height:68px">How Can We Help?</div>
    <div class="btn-quote">START FREE QUOTE</div>
  </form>
</section>

<section>
  <h2 class="abs display about-title">ABOUT US</h2>
  <p class="abs about-sub">From humble beginnings</p>
  <div class="abs about-copy">
    <p>In 2016 Reid Hollis started helping people with their home improvement projects. HIs very first job was installing window trim for a wonderful homeowner in Cedar Ridge MN. He did his best work and made sure he treated his first customer like family. Afterall, his first customer was Marla Hollis, his Mom.</p>
    <p>Today, Reid and the Stoneguard Construction team are helping homeowners around Minnesota; carrying the spirit of his first job onto every job they touch.</p>
  </div>
  <div class="abs btn-gray" style="left:113px;top:1143px;width:128px">Learn More</div>
  <div class="abs about-photo" role="img" aria-label="Roofer in a green shirt and cap laying orange clay roof tiles"></div>
</section>

<section>
  <div class="abs services"></div>
  <h2 class="abs display section-title" style="top:1346px">WHAT WE DO</h2>

  <div class="abs service-photo" style="left:111px;top:1440px;background:linear-gradient(160deg,#9cc3e6 0%,#c9dbe9 35%,#3d434c 55%,#2a2e34 100%)" role="img" aria-label="Dark shingle roof with skylights under a blue sky"></div>
  <h3 class="abs service-name" style="left:109px;top:1778px">ROOFING</h3>
  <p class="abs service-copy" style="left:109px;top:1821px">Architectural shingles are the most cost effective choice in roofing, that is why they are also the most common choice. At Stoneguard Construction we specialize in replacing architectural shingle roofing.</p>
  <div class="abs btn-outline" style="left:110px;top:1946px">Learn More</div>

  <div class="abs service-photo" style="left:621px;top:1440px;background:linear-gradient(180deg,#c8a978 0%,#b99c74 50%,#8d7a66 100%)" role="img" aria-label="Worker in overalls installing beige vinyl siding on a wall"></div>
  <h3 class="abs service-name" style="left:619px;top:1778px">SIDING</h3>
  <p class="abs service-copy" style="left:619px;top:1821px">Vinyl siding is a great option to give your home’s exterior a beautiful makeover. A typical vinyl siding replacement can be completed in 3-5 days and costs about 15-25k.</p>
  <div class="abs btn-outline" style="left:620px;top:1946px">Learn More</div>

  <div class="abs service-photo" style="left:111px;top:2047px;background:linear-gradient(160deg,#5b5f66 0%,#c9bda8 40%,#2f66c4 75%,#1d4fb0 100%)" role="img" aria-label="Worker in a blue cap and shirt fitting a gutter under a metal roof"></div>
  <h3 class="abs service-name" style="left:109px;top:2385px">GUTTERS</h3>
  <p class="abs service-copy" style="left:109px;top:2428px">We offer 5” or 6” aluminum seamless gutters for your home or business. Gutters are usually an afterthought, but they perform the vital function of carrying water away from your foundation.</p>
  <div class="abs btn-outline" style="left:110px;top:2529px">Learn More</div>

  <div class="abs service-photo" style="left:621px;top:2047px;background:linear-gradient(90deg,#e9e2d8 0%,#d9d2c6 45%,#b9c98a 80%,#e6ddcf 100%)" role="img" aria-label="Installer carrying a white window frame beside an opening in the wall"></div>
  <h3 class="abs service-name" style="left:619px;top:2385px">WINDOWS</h3>
  <p class="abs service-copy" style="left:619px;top:2428px">At this time, we only offer window replacement as part of a siding replacement job and not as a standalone service. We offer Harlow and Kessel replacement windows.</p>
  <div class="abs btn-outline" style="left:620px;top:2529px">Learn More</div>

  <div class="abs btn-gray" style="left:536px;top:2611px;width:128px">View All</div>
</section>

<section>
  <h2 class="abs display section-title" style="top:2798px">SOME OF OUR TRUSTLINE REVIEWS</h2>

  <article class="abs review-card" style="left:111px;top:2876px">
    <span class="mark">“</span>
    <p class="text">Lorem ipsum dolor sit amet, consectetur adipiscing elit, sed do eiusmod tempor incididunt ut labore et dolore magna aliqua. Ut enim ad minim veniam, quis nostrud exercitation</p>
    <p class="name">Dana Whitlock</p>
    <p class="stars">★★★★★</p>
  </article>
  <article class="abs review-card" style="left:446px;top:2876px">
    <span class="mark">“</span>
    <p class="text">Lorem ipsum dolor sit amet, consectetur adipiscing elit, sed do eiusmod tempor incididunt ut labore et dolore magna aliqua. Ut enim ad minim veniam, quis nostrud exercitation</p>
    <p class="name">Brookside Pet Supply</p>
    <p class="stars">★★★★★</p>
  </article>
  <article class="abs review-card" style="left:779px;top:2876px">
    <span class="mark">“</span>
    <p class="text">Lorem ipsum dolor sit amet, consectetur adipiscing elit, sed do eiusmod tempor incididunt ut labore et dolore magna aliqua. Ut enim ad minim veniam, quis nostrud exercitation</p>
    <p class="name">Martin Caldwell</p>
    <p class="stars">★★★★★</p>
  </article>

  <div class="abs arrow" style="left:0;top:3010px;background:#9a9b9e">
    <svg width="14" height="26" viewBox="0 0 14 26"><path d="M12 2 2 13l10 11" fill="none" stroke="#fff" stroke-width="2"/></svg>
  </div>
  <div class="abs arrow" style="left:1160px;top:3010px;background:var(--dark)">
    <svg width="14" height="26" viewBox="0 0 14 26"><path d="M2 2l10 11L2 24" fill="none" stroke="#fff" stroke-width="2"/></svg>
  </div>
</section>

<footer>
  <div class="abs site-footer"></div>
  <div class="abs brand" style="left:460px;top:3392px">
    <span class="brand-dot" style="width:60px;height:60px"></span>
    <span class="brand-name" style="font-size:19px">STONEGUARD<br>CONSTRUCTION</span>
  </div>
  <p class="abs footer-links" style="color:var(--white)">HOME &nbsp;|&nbsp; WHAT WE DO &nbsp;|&nbsp; ABOUT US &nbsp;|&nbsp; CONTACT US</p>
  <div class="abs social"><span></span><span></span><span></span><span></span><span></span></div>
  <div class="abs footer-rule"></div>
  <p class="abs copyright" style="color:var(--white)">©Copyrights 2024 Stoneguard Construction &nbsp;| &nbsp; All Rights Reserved</p>
</footer>

</body>
</html>
```